Very new and innovative Web design for Property managers of Vacation rentals

We are looking for a new website design for travel agencies and property managers specialised on vacation rentals business, holiday villas and apartments.

The end users of this website are travellers who are looking for a vacation home for their next holiday: this is the reason why the website must be easy to use, attractive, professional, possibly elegant and focused on get new reservations.

This is a draft of our current website: https://intro3.kelumsito.com/
Please consider that we would like to have proposals with a totally different and innovative layout, surprise us!

These are the pages of the website:
• Homepage: feel free to redesign all the homepage as you wish, surprise us with something very new! Please consider that Property manager/Travel agencies usually want to have the opportunity to put in evidence groups of houses with specific characteristics (eg. villas with private swimming pool, apartment in big/small towns, villas with air co, etc…), destinations and tourist areas, and sometimes experiences or activities (please consider that the website layout must be suitable even if some of the previous sections are not used).
• Search page: we’d like to organise the results of the search page in three different ways:
o Grid
o Map
o List
• Property page: to illustrate the characteristics, descriptions, images, …. of the property. It is very important to put in evidence images of the property and to maintain the booking form (and the other call to action bottom – eg. whatsapp) always visible
• Custom pages: static pages composed usually by text, images and call to actions
• Contact us (general form)
• Info request (specific of a property form)
• Booking process
• Blog, organised in four pages:
o Home Page – introduction to the blog
o List of articles
o Single article
o Site Map (presentation of categories and sub-categories)

If possible, we’d prefer to receive the material in Adobe XD or similar so that we can obtain the three versions:
- smartphone
- tablet
- desktop

The website will be then developed in Bootstrap: as a result we’ll need the icons in SVG format (or the library used)

In attachment you can find the map of the website pages

```html
<!DOCTYPE html>
<html lang="en">
<head>
<meta charset="utf-8">
<title>Casolare – Desktop and Mobile Version</title>
<link rel="stylesheet" href="https://fonts.googleapis.com/css2?family=Montserrat:wght@300;400;500;600&family=Playfair+Display:wght@400;500&display=swap">
<style>
:root{
  --green:#17b67e;
  --green-dark:#0e9a69;
  --top-a:#0a5a44;
  --top-b:#083a2d;
  --sage:#5e7c71;
  --ink:#1d1f24;
  --muted:#8a8f99;
  --band:#eceef3;
  --panel:#f6f7f9;
  --line:#dfe2e8;
  --footer:#151515;
  --white:#ffffff;
}
*{box-sizing:border-box;margin:0;padding:0}
html,body{width:951px;height:1200px;overflow:hidden}
body{font-family:"Montserrat",sans-serif;color:var(--ink);background:var(--sage);position:relative}
.scene-top{position:absolute;left:0;top:0;width:951px;height:462px;background:radial-gradient(ellipse at 60% 30%,var(--top-a),var(--top-b))}
.brand{position:absolute;left:111px;top:44px;display:flex;align-items:center;gap:12px}
.brand-mark{width:34px;height:34px;background:var(--green);border-radius:4px}
.brand-name{font-family:"Montserrat",sans-serif;font-weight:300;font-size:34px;color:var(--white);letter-spacing:-.5px}
.label-vertical{position:absolute;font-family:"Playfair Display",serif;font-weight:400;color:var(--white);white-space:nowrap;line-height:1;font-size:64px;z-index:2}
.label-desktop{left:26px;top:1028px;transform:rotate(-90deg);transform-origin:left top}
.label-mobile{left:796px;top:412px;transform:rotate(90deg) translateY(-100%);transform-origin:left top}

/* shared page pieces */
.page{position:absolute;background:var(--white);transform-origin:left top;overflow:hidden}
.abs{position:absolute}
.logo{display:flex;align-items:center;gap:5px}
.logo i{display:block;background:var(--green);border-radius:2px}
.logo span{font-weight:400;color:var(--ink)}
.photo{position:absolute}
.photo-pool{background:linear-gradient(180deg,#b9cbd8 0%,#e6ecef 35%,#4b5a55 55%,#2d8fc8 75%,#1f6ea4 100%)}
.photo-garden{background:linear-gradient(180deg,#6f8a5c 0%,#4f6e3c 50%,#7d8f7a 70%,#a07c4e 100%)}
.photo-villa{background:linear-gradient(180deg,#7d8f55 0%,#a46a4c 40%,#3f6a3a 60%,#3c9bd1 85%,#2577ad 100%)}
.serif{font-family:"Playfair Display",serif}
.btn-green{background:var(--green);color:var(--white);font-weight:600;display:flex;align-items:center;justify-content:center}

/* desktop page (built at 684 x 880, scaled) */
.desktop{left:95px;top:548px;width:684px;height:880px;transform:scale(.557)}
.desk-topbar{left:489px;top:0;width:195px;height:22px;background:var(--green);color:var(--white);font-size:7px;font-weight:600;display:flex;align-items:center;gap:18px;padding-left:8px;clip-path:polygon(6% 0,100% 0,100% 100%,0 100%)}
.desk-nav{top:34px;left:324px;display:flex;gap:0;font-size:7.5px;color:#333}
.desk-nav span{position:absolute;white-space:nowrap}
.desk-search{left:0;top:53px;width:684px;height:34px;background:var(--band)}
.field{position:absolute;top:8px;font-size:5.5px;color:#333;line-height:1.3}
.field b{display:block;font-size:7px;font-weight:400}
.field-sep{position:absolute;top:0;width:1px;height:34px;background:var(--line)}
.desk-sub{left:0;top:87px;width:684px;height:44px;background:var(--band)}
.filters{left:63px;top:107px;width:129px;height:553px;background:var(--panel)}
.filters-head{height:23px;background:var(--white);color:var(--green);font-size:6.5px;padding:9px 9px 0}
.f-item{position:absolute;left:10px;font-size:6px;color:#333;display:flex;align-items:center;gap:6px}
.radio{width:8px;height:8px;border:1px solid #c7cbd2;border-radius:50%;background:var(--white)}
.radio.on{border-color:var(--green);box-shadow:inset 0 0 0 2px var(--white);background:var(--green)}
.check{width:8px;height:8px;border:1px solid #c7cbd2;background:var(--white)}
.f-title{position:absolute;left:9px;font-size:6.5px;color:#333}
.view-tabs{left:490px;top:107px;width:130px;height:23px;background:var(--white);font-size:5px;display:flex}
.view-tabs span{flex:1;display:flex;align-items:center;justify-content:center;gap:3px}
.view-tabs .active{border-bottom:2px solid var(--green)}
.card{position:absolute;left:206px;width:414px;height:149px;background:var(--white);box-shadow:0 1px 4px rgba(0,0,0,.12)}
.card .photo{left:0;top:0;width:141px;height:149px}
.card-body{position:absolute;left:154px;top:12px;width:245px}
.card-title{font-size:11px;color:#222}
.card-meta{font-size:5.5px;color:var(--muted);margin-top:5px;line-height:1.5}
.card-rule{height:1px;background:var(--line);margin:4px 0}
.card-text{font-size:6px;color:#555;line-height:1.55}
.card-foot{position:absolute;left:141px;top:108px;width:273px;height:41px;background:var(--panel)}
.price{position:absolute;left:13px;top:8px;font-size:5px;color:#555;line-height:1.2}
.price b{display:block;font-size:8px;color:#222;font-weight:600}
.card-foot .btn-green{position:absolute;right:13px;top:8px;width:54px;height:23px;font-size:6.5px}
.pager{display:flex}
.pager span{width:15px;height:15px;border:1px solid var(--line);font-size:6px;display:flex;align-items:center;justify-content:center;margin-left:-1px;background:var(--white)}
.desk-footer{left:0;top:696px;width:684px;height:184px;background:var(--footer);color:#cfcfcf}
.fcol{position:absolute;top:30px;font-size:6px;line-height:2.65}
.fcol h4{font-family:"Playfair Display",serif;font-weight:400;font-size:9.5px;color:var(--white);line-height:1;margin-bottom:8px}
.dot{display:inline-block;width:10px;height:10px;border-radius:50%;background:var(--white);vertical-align:middle;margin-right:6px}
.copy{position:absolute;left:0;width:684px;top:146px;text-align:center;font-size:5.5px;color:#bbb}

/* mobile page (built at 218 x 1648, scaled) */
.mobile{left:656px;top:237px;width:218px;height:1648px;transform:scale(.557)}
.m-bar{left:0;top:36px;width:218px;height:29px;background:var(--green)}
.m-tools{left:5px;top:77px;width:208px;height:25px;display:flex;border:1px solid var(--line)}
.m-tools span{flex:1;display:flex;align-items:center;justify-content:center;gap:4px;font-size:7px;border-right:1px solid var(--line)}
.m-select{left:5px;top:130px;width:208px;height:25px;border:1px solid var(--line);font-size:6.5px;color:#666;padding:8px 7px}
.m-text{left:5px;width:208px;font-size:6.5px;color:#555;line-height:1.65}
.m-strip{left:5px;width:208px;height:53px;background:var(--panel)}
.m-strip .price{left:11px;top:9px;font-size:7px}
.m-strip .price b{font-size:9.5px}
.m-strip .btn-green{position:absolute;right:11px;top:14px;width:54px;height:23px;font-size:6.5px}
.m-footer{left:0;top:1037px;width:218px;height:611px;background:var(--footer);color:#cfcfcf;padding:18px 5px}
.m-footer h4{font-family:"Playfair Display",serif;font-weight:400;font-size:11.5px;color:var(--white);margin:0 0 10px}
.m-footer p{font-size:8px;line-height:2.7}
</style>
</head>
<body>

<div class="scene-top"></div>

<div class="brand">
  <span class="brand-mark"></span>
  <span class="brand-name">Casolare</span>
</div>

<!-- DESKTOP PAGE -->
<section class="page desktop" aria-label="Desktop search results page">
  <div class="abs desk-topbar"><span>&#9711; LOGIN</span><span>&#9825; WHISHLIST</span><span>EN &#709;</span></div>
  <div class="abs logo" style="left:63px;top:14px"><i style="width:18px;height:18px"></i><span style="font-size:15px">Casolare</span></div>
  <nav class="abs desk-nav">
    <span style="left:0;color:var(--green)">HOME</span>
    <span style="left:54px">SEARCH</span>
    <span style="left:116px">PROPERTY</span>
    <span style="left:186px">CUSTOM</span>
    <span style="left:249px">CONTACT US</span>
  </nav>

  <div class="abs desk-search">
    <div class="field" style="left:63px">DATES<b>From - To</b></div>
    <div class="field-sep" style="left:182px"></div>
    <div class="field" style="left:194px">TOWN<b>-all-</b></div>
    <div class="field-sep" style="left:312px"></div>
    <div class="field" style="left:324px">ADULTS:<b>- - &nbsp;&nbsp;&nbsp;&nbsp;&nbsp;&nbsp;&nbsp;&nbsp;&nbsp;&nbsp;&#709;</b></div>
    <div class="field-sep" style="left:377px"></div>
    <div class="field" style="left:389px">CHILDREN:<b>- - &nbsp;&nbsp;&nbsp;&nbsp;&nbsp;&nbsp;&nbsp;&nbsp;&nbsp;&nbsp;&#709;</b></div>
    <div class="field-sep" style="left:441px"></div>
    <div class="field" style="left:453px">BEDROOMS:<b>- - &nbsp;&nbsp;&nbsp;&nbsp;&nbsp;&nbsp;&nbsp;&nbsp;&nbsp;&nbsp;&#709;</b></div>
    <div class="field-sep" style="left:507px"></div>
    <div class="abs btn-green" style="left:553px;top:5px;width:67px;height:23px;font-size:7px">SEARCH</div>
  </div>
  <div class="abs desk-sub"></div>

  <aside class="abs filters">
    <div class="filters-head">FILTERS</div>
    <div class="f-title" style="top:36px;font-size:6px">Clear all</div>
    <div class="f-title" style="top:47px;font-size:4.5px;color:var(--muted)">TYPE OF ACCOMMODATION</div>
    <div class="f-item" style="top:74px"><i class="radio on"></i>All</div>
    <div class="f-item" style="top:92px"><i class="radio"></i>GardenNear</div>
    <div class="f-item" style="top:110px"><i class="radio"></i>VillageInternet</div>
    <div class="f-item" style="top:127px"><i class="radio"></i>Baby Bed</div>
    <div class="f-item" style="top:145px"><i class="radio"></i>Maid</div>
    <div class="f-item" style="top:162px"><i class="radio"></i>Parking</div>
    <div class="f-item" style="top:180px"><i class="radio"></i>Swimmingpool</div>
    <div class="f-item" style="top:198px"><i class="radio"></i>Weddings</div>
    <div class="f-item" style="top:215px"><i class="radio"></i>Breakfast</div>
    <div class="f-item" style="top:233px"><i class="radio"></i>Internet Wifi</div>
    <div class="f-title" style="top:268px">CATEGORY</div>
    <div class="f-item" style="top:285px"><i class="check"></i>Sevilla</div>
    <div class="f-title" style="top:314px">MAIN FEATURES</div>
    <div class="f-item" style="top:331px"><i class="check"></i>GardenNear</div>
    <div class="f-item" style="top:348px"><i class="check"></i>VillageInternet</div>
    <div class="f-item" style="top:366px"><i class="check"></i>Baby Bed</div>
    <div class="f-item" style="top:383px"><i class="check"></i>Maid</div>
    <div class="f-item" style="top:400px"><i class="check"></i>Parking</div>
    <div class="f-item" style="top:418px"><i class="check"></i>Swimmingpool</div>
    <div class="f-item" style="top:435px"><i class="check"></i>Weddings</div>
    <div class="f-item" style="top:452px"><i class="check"></i>Breakfast</div>
    <div class="f-item" style="top:469px"><i class="check"></i>Internet Wifi</div>
    <div class="f-title" style="top:500px;font-size:5.5px">REFERENCE N° / NAME</div>
    <div class="abs" style="left:9px;top:512px;width:110px;height:19px;background:var(--white);border:1px solid var(--line);font-size:5.5px;color:var(--muted);padding:6px 6px">Search<span style="float:right;color:#555">&#9906;</span></div>
  </aside>

  <div class="abs view-tabs">
    <span>&#8759; GRID</span><span class="active">&#9776; LIST</span><span>&#9906; MAP</span>
  </div>

  <article class="card" style="top:151px">
    <div class="photo photo-pool" role="img" aria-label="Modern villa with swimming pool"></div>
    <div class="card-body">
      <div class="card-title serif">Agriturismo Le Querce</div>
      <div class="card-meta">Country House / Farm House<br>Accommodations: 2 Sleeps: 7 Bedrooms: 2 Bathrooms: 2</div>
      <div class="card-rule"></div>
      <div class="card-text">Il casale è immerso nella campagna toscana ma a soli 3 km dal paese più vicino dove potete trovare tutti i negozi con le principali comodità.</div>
    </div>
    <div class="card-foot"><div class="price">from<b>€ 800</b>per week</div><div class="btn-green">+ Info</div></div>
  </article>

  <article class="card" style="top:312px">
    <div class="photo photo-garden" role="img" aria-label="Poolside deck with hat and towel in a green garden"></div>
    <div class="card-body">
      <div class="card-title serif">Podere Il Colle</div>
      <div class="card-meta">Apartment<br>Accommodations: 4 Sleeps: 27 Bedrooms: 10 Bathrooms: 6</div>
      <div class="card-rule"></div>
      <div class="card-text">The owners offer a wide choice of Extra Services to make you feel welcome and to help you discover Tuscany in a "non touristy" way. You can choose from Cookery nights with the owners...</div>
    </div>
    <div class="card-foot"><div class="price">from<b>€ 3400</b>per week</div><div class="btn-green">+ Info</div></div>
  </article>

  <article class="card" style="top:473px">
    <div class="photo photo-villa" role="img" aria-label="Stone villa with pool among olive trees"></div>
    <div class="card-body">
      <div class="card-title serif">Appartamento Laguna</div>
      <div class="card-meta">Villa<br>Sleeps: 15 Bedrooms: 7 Bathrooms: 5 Floor Area: 300 m2</div>
      <div class="card-rule"></div>
      <div class="card-text">This detached villa features a terrace and a garden with a seasonal outdoor pool and a barbecue. The villa features air conditioning and free WiFi.</div>
    </div>
    <div class="card-foot"><div class="price">from<b>€ 4200</b>per week</div><div class="btn-green">+ Info</div></div>
  </article>

  <div class="abs" style="left:206px;top:648px;font-size:5.5px;color:#666">Showing 1 - 6 of 176 accommodations</div>
  <div class="abs pager" style="left:544px;top:644px"><span>1</span><span>2</span><span>3</span><span>4</span><span>&#8250;</span></div>

  <footer class="abs desk-footer">
    <div class="abs logo" style="left:63px;top:75px"><i style="width:14px;height:14px"></i><span style="font-size:12px;color:var(--white)">Casolare</span></div>
    <div class="fcol" style="left:191px"><h4>Quick Links</h4>Home<br>Search<br>Property<br>Custom<br>Contact Us</div>
    <div class="fcol" style="left:300px"><h4>Company</h4>Privacy Policies<br>Reservation Policies<br>Cookie Policy</div>
    <div class="fcol" style="left:414px;line-height:1.4"><h4>Contact Us</h4>&#9906; Via dei Cipressi 7 50100<br>&nbsp;&nbsp;&nbsp;Valdorcia, Siena (Italy)<br><br>&#9990; +39 055 0000123<br><br>&#9993; hello@casolare-stays.com</div>
    <div class="fcol" style="left:566px;line-height:2.4"><h4>Follow Us</h4><span class="dot"></span>Friendbook<br><span class="dot"></span>Chirper<br><span class="dot"></span>Snapgram</div>
    <div class="copy">Copyright © 2021 <b style="color:var(--white)">Casolare</b>. All rights reserved.</div>
  </footer>
</section>

<!-- MOBILE PAGE -->
<section class="page mobile" aria-label="Mobile search results page">
  <div class="abs logo" style="left:56px;top:6px"><i style="width:16px;height:16px"></i><span style="font-size:14px">Casolare</span></div>
  <div class="abs m-bar">
    <svg class="abs" style="left:8px;top:10px" width="18" height="10" viewBox="0 0 18 10"><path d="M0 1h18M0 5h18M0 9h18" stroke="#fff" stroke-width="1.5"/></svg>
    <span class="abs" style="right:10px;top:9px;font-size:7.5px;color:#fff;font-weight:600">&#9711; &#9825; EN &#709;</span>
  </div>
  <div class="abs m-tools"><span>&#8801; Filter</span><span>&#9906; Search</span></div>
  <div class="abs" style="left:197px;top:108px;width:16px;height:16px;border:1px solid var(--line);font-size:8px;text-align:center;line-height:15px">&#9906;</div>
  <div class="abs m-select">Find number<span style="float:right">&#709;</span></div>
  <div class="photo photo-pool" style="left:5px;top:168px;width:208px;height:219px" role="img" aria-label="Modern villa with swimming pool"></div>

  <div class="abs m-text" style="top:453px">il casale è immerso nella campagna toscana ma a soli 3 km dal paese più vicino dove potete trovare tutti i negozi con le principali comodità.</div>
  <div class="abs m-strip" style="top:507px"><div class="price">from<b>€ 800</b>per week</div><div class="btn-green">+ Info</div></div>

  <div class="photo photo-garden" style="left:5px;top:578px;width:208px;height:219px" role="img" aria-label="Poolside deck with hat and towel in a green garden"></div>
  <div class="abs serif" style="left:5px;top:811px;font-size:11px">Podere Il Colle</div>
  <div class="abs m-text" style="top:834px;font-size:6px;color:var(--muted);line-height:1.9">Apartment<br>Accommodations: 4 Sleeps: 27 Bedrooms: 10 Bathrooms: 6</div>
  <div class="abs m-text" style="top:863px;font-size:6px">The owners offer a wide choice of Extra Services to make you feel welcome and to help you discover Tuscany in a "non touristy" way. You can choose from Cookery nights with the owners...</div>
  <div class="abs m-strip" style="top:920px"><div class="price">from<b>€ 3400</b>per week</div><div class="btn-green">+ Info</div></div>
  <div class="abs pager" style="left:108px;top:992px"><span style="width:22px;height:21px">1</span><span style="width:22px;height:21px">2</span><span style="width:22px;height:21px">3</span><span style="width:22px;height:21px">4</span><span style="width:22px;height:21px">&#8250;</span></div>

  <footer class="abs m-footer">
    <h4>Quick Links</h4>
    <p>Home<br>Search<br>Property<br>Custom<br>Contact Us</p>
    <h4 style="margin-top:10px">Company</h4>
    <p>Privacy Policies<br>Reservation Policies<br>Cookie Policy</p>
    <h4 style="margin-top:10px">Contact Us</h4>
    <p style="line-height:1.4">&#9906; Via dei Cipressi 7 50100<br>&nbsp;&nbsp;&nbsp;Valdorcia, Siena (Italy)</p>
    <p style="margin-top:8px">&#9990; +39 055 0000123</p>
    <p>&#9993; hello@casolare-stays.com</p>
    <h4 style="margin-top:14px">Follow Us</h4>
    <p style="line-height:2.9"><span class="dot" style="width:13px;height:13px"></span>Friendbook<br><span class="dot" style="width:13px;height:13px"></span>Chirper<br><span class="dot" style="width:13px;height:13px"></span>Snapgram</p>
    <div class="logo" style="justify-content:center;margin-top:52px"><i style="width:14px;height:14px"></i><span style="font-size:12px;color:var(--white)">Casolare</span></div>
    <p style="text-align:center;font-size:5.5px;line-height:2.4;color:#bbb">Copyright © 2021 <b style="color:var(--white)">Casolare</b>. All rights reserved.</p>
  </footer>
</section>

<div class="label-vertical label-desktop">Desktop Version</div>
<div class="label-vertical label-mobile">Mobile Version</div>

</body>
</html>
```